Reach Crafters Unique Marketing Website Design

I am starting a new company that is a thought leader in the marketing consulting space. The company is called Reach Crafters. We intend to build a Wordpress site on the Astra Theme with the Spectra builder. Our goal is to become the leading voice that empowers high-ticket service business leaders to become Reach Crafters by equipping them with the cutting-edge frameworks and decision grade intelligence taught in leading business schools. What we are looking for is a website design that is clean and professional, making some use of white space well also being eye catching and distinctive in the consulting space. We will probably want to have a video on the homepage not in the hero section, but just below to explain the company and what we do. Our tagline is "Be found. Be chosen." I have attached a brand guide with some messaging, our typography choices, and our color system. The full site will have a primary nav that is four pages - About us, Services, Insights (essentially a blog), and Contact Us. The goal of this project is to develop an art direction that I can give to a designer to build loads of new pages.

Target Market(s)

Business owners (mostly male) from 30-60 years old, looking to fix their sales and marketing funnel.

Industry/Entity Type

Marketing consulting

Font styles to use
Sans Serif

Requirements
Must have
• A clean, professional design that builds trust with owners of high-ticket service businesses. We need a space for explainer video, and sections that tell prospects what we do. Would also like to have a blog carousel.
Nice to have
• Social feeds, if possible. See attached documents for colors and fonts.
Should not have
• Our feel is professional enough to be trustworthy, but unique enough to be memorable. Cartoon ideas do not meet the professional test, and we do not want the website to appear feminine.

```html
<!DOCTYPE html>
<html lang="en">
<head>
<meta charset="utf-8">
<title>Reach Crafters — Marketing Consulting</title>
<link href="https://fonts.googleapis.com/css2?family=Inter:ital,wght@0,400;0,500;0,600;0,700;1,400;1,500&family=Oswald:wght@300;400;500&display=swap" rel="stylesheet">
<style>
:root{
  --blue:#2d5bf0;
  --blue-dark:#1e46d6;
  --navy:#0d1a33;
  --ink:#1b1f2a;
  --body:#555b66;
  --soft:#f6f6f7;
  --line:#e6e8ec;
  --white:#ffffff;
  --star:#f2762e;
}
*{box-sizing:border-box;margin:0;padding:0}
html,body{width:1200px;height:4850px;overflow:hidden}
body{font-family:'Inter',sans-serif;color:var(--body);background:var(--white);font-size:13px;line-height:1.6}
.heading{font-family:'Oswald',sans-serif;font-weight:400;color:var(--ink);letter-spacing:.2px}
.accent{color:var(--blue)}
.rule{width:46px;height:2px;background:var(--blue);margin:14px auto 0}
.btn{display:inline-flex;align-items:center;gap:8px;background:var(--blue);color:var(--white);font-size:13px;font-weight:500;padding:0 20px;height:40px;text-decoration:none}
.arrow{font-size:14px}
.wrap{width:918px;margin:0 auto}
.center{text-align:center}

/* header */
.site-header{height:78px;display:flex;align-items:center;justify-content:space-between;padding:0 70px;background:var(--white);border-bottom:1px solid var(--line)}
.brand-name{font-family:'Inter',sans-serif;font-weight:700;font-size:27px;color:var(--navy);letter-spacing:.3px;line-height:1}
.nav{display:flex;align-items:center;gap:50px;font-size:12.5px;color:var(--body)}
.nav .btn{height:36px;font-size:12.5px;padding:0 16px}

/* hero */
.hero{height:544px;position:relative;background:linear-gradient(100deg,#15181f 0%,#262a33 38%,#5a5f6a 62%,#8c8f96 100%);overflow:hidden}
.hero-photo{position:absolute;left:450px;top:0;width:750px;height:544px;background:linear-gradient(90deg,rgba(40,44,52,0) 0%,#6e737c 40%,#b9bcc2 100%)}
.hero-copy{position:absolute;left:72px;top:120px;width:400px;color:var(--white)}
.hero-kicker{font-style:italic;font-size:17px;font-weight:500}
.hero-title{font-family:'Oswald',sans-serif;color:var(--white);line-height:1.15;margin-top:14px}
.hero-title .l1{font-size:40px;font-weight:500}
.hero-title .l1 u{text-decoration-color:var(--blue);text-decoration-thickness:4px;text-underline-offset:6px}
.hero-title .l2{font-size:38px;font-weight:300;display:block}
.hero-text{font-size:13px;line-height:1.7;margin-top:20px}
.hero .btn{margin-top:28px}

/* pillars */
.pillars{height:554px;background:var(--soft);padding-top:60px}
.sec-title{font-size:38px;text-align:center;line-height:1.2}
.sub{text-align:center;margin-top:20px;font-size:13.5px}
.card-row{display:flex;gap:35px;margin-top:28px}
.card{flex:1;background:var(--white);box-shadow:0 4px 18px rgba(20,30,60,.06)}
.pillar{height:283px;padding:30px 28px}
.pillar svg{width:62px;height:62px}
.pillar h3{font-size:16px;font-weight:600;color:var(--ink);margin-top:22px}
.pillar hr{border:0;border-top:1px solid var(--line);margin:12px 0}
.pillar p{font-size:11.5px;line-height:1.7}

/* video */
.video{height:816px;padding-top:62px}
.video .sub{width:640px;margin:20px auto 0}
.video-frame{margin-top:40px;height:520px;padding:8px;background:var(--white);box-shadow:0 4px 24px rgba(20,30,60,.14)}
.video-still{width:100%;height:100%;position:relative;background:linear-gradient(135deg,#6a5a4f 0%,#3b3f4a 45%,#8a6f5e 100%);display:flex;align-items:center;justify-content:center}
.play{width:62px;height:62px;border-radius:50%;background:var(--blue);display:flex;align-items:center;justify-content:center;box-shadow:0 0 0 10px rgba(255,255,255,.25)}

/* stats */
.stats{height:395px;background:linear-gradient(135deg,var(--navy) 0%,#0a1428 60%,#132445 100%);display:flex;justify-content:center;gap:44px;padding-top:78px}
.stat{width:192px;text-align:center;color:var(--white)}
.stat-ring{position:relative;width:192px;height:192px}
.stat-ring svg{position:absolute;inset:0}
.stat-value{position:absolute;inset:0;display:flex;align-items:center;justify-content:center;font-family:'Oswald',sans-serif;font-size:38px;font-weight:500;color:var(--white)}
.stat-label{margin-top:26px;font-size:14.5px}

/* about */
.about{height:563px;display:flex;gap:66px;padding:78px 0 0 141px}
.about-photo{width:417px;height:408px;background:linear-gradient(90deg,#e8edf2 0%,#cdd4dc 50%,#f1f2f3 100%)}
.about-copy{width:436px;padding-top:40px}
.about-title{font-size:38px;line-height:1.1}
.about-title .brand{font-family:'Inter',sans-serif;font-weight:700;font-size:32px;color:var(--navy)}
.about-copy h4{font-size:14px;font-weight:600;color:var(--ink);margin-top:22px}
.about-copy p{font-size:12px;line-height:1.75;margin-top:12px}
.about-copy .btn{margin-top:22px}

/* testimonials */
.reviews{height:565px;background:var(--soft);padding-top:62px}
.review{height:255px;padding:24px 26px;position:relative}
.stars{color:var(--star);font-size:15px;letter-spacing:2px}
.quote-mark{position:absolute;right:26px;top:12px;font-family:'Oswald',sans-serif;font-size:60px;line-height:1;color:#c4cef8}
.review p{font-style:italic;font-size:11.5px;line-height:1.95;margin-top:12px}
.author{display:flex;align-items:center;gap:12px;margin-top:16px}
.avatar{width:32px;height:32px;border-radius:50%;background:var(--blue);color:var(--white);font-weight:700;font-size:14px;display:flex;align-items:center;justify-content:center}
.author strong{display:block;font-size:14px;font-weight:600;color:var(--ink);line-height:1.3}
.author span{font-size:10px;color:var(--body)}
.dots{display:flex;justify-content:center;gap:8px;margin-top:37px}
.dots i{width:6px;height:6px;border-radius:50%;background:#c9ccd3}
.dots i.on{background:var(--blue)}

/* blog */
.blog{height:660px;padding-top:62px}
.blog .card-row{margin-top:44px}
.post{height:357px;box-shadow:none;background:none}
.post-img{height:150px;position:relative}
.post-img.a{background:linear-gradient(135deg,#9c8a77,#e9e3d9 60%,#bfb3a2)}
.post-img.b{background:linear-gradient(135deg,#f1f3f6,#cdd7e6 55%,#8ea3c4)}
.post-img.c{background:linear-gradient(135deg,#c9c2b8,#6f6a66 55%,#d8d3cc)}
.date{position:absolute;right:4px;top:4px;width:34px;height:42px;background:var(--blue);color:var(--white);text-align:center;line-height:1}
.date b{display:block;font-family:'Oswald',sans-serif;font-size:20px;font-weight:500;padding-top:4px}
.date small{font-size:9px}
.post-body{background:var(--white);margin:0 12px;padding:18px 20px 20px;box-shadow:0 6px 18px rgba(20,30,60,.08);height:207px}
.post-body h3{font-size:14px;font-weight:600;color:var(--ink);line-height:1.4}
.post-body p{font-size:11.5px;line-height:1.75;margin-top:12px}
.more{display:inline-block;margin-top:10px;font-size:12px;font-weight:500;color:var(--blue)}
.blog .btn{margin-top:30px}

/* cta */
.cta{height:322px;background:linear-gradient(120deg,var(--blue-dark) 0%,var(--blue) 55%,#3f6af5 100%);color:var(--white);text-align:center;padding-top:66px}
.cta h2{font-family:'Oswald',sans-serif;font-weight:300;font-size:40px;color:var(--white);line-height:1.2}
.cta h2 b{font-weight:500}
.cta p{font-size:13.5px;width:520px;margin:16px auto 0;line-height:1.7}
.btn-white{background:var(--white);color:var(--blue);margin-top:24px}

/* footer */
.site-footer{height:353px;background:var(--navy);color:#d6dbe6;padding:62px 0 0 141px;position:relative}
.foot-cols{display:flex}
.foot-col h5{font-size:15px;font-weight:600;color:var(--white)}
.foot-col h5::after{content:"";display:block;width:24px;height:2px;background:var(--blue);margin-top:10px}
.foot-col ul{list-style:none;margin-top:18px}
.foot-col li{font-size:12px;margin-bottom:10px}
.foot-brand{width:308px}
.foot-brand .brand-name{color:var(--white);font-size:20px}
.foot-brand p{font-size:12px;margin-top:28px;width:240px}
.follow{display:flex;align-items:center;gap:8px;margin-top:24px;font-size:12px}
.follow i{width:24px;height:24px;border-radius:50%;border:1.5px solid #8796b5}
.follow i.on{background:var(--blue);border-color:var(--blue)}
.contact li{display:flex;gap:14px;align-items:flex-start;margin-bottom:18px;width:230px}
.c-icon{flex:none;width:30px;height:30px;border-radius:50%;background:var(--white);display:flex;align-items:center;justify-content:center}
.legal{position:absolute;bottom:12px;left:0;right:0;text-align:center;font-size:10.5px;color:#b8c0d2}
</style>
</head>
<body>

<header class="site-header">
  <div class="brand-name">REACH CRAFTERS</div>
  <nav class="nav">
    <span>About Us</span><span>Services</span><span>Insights</span>
    <a class="btn" href="#">Contact Us</a>
  </nav>
</header>

<section class="hero">
  <div class="hero-photo" role="img" aria-label="Photo of two smiling business leaders in shirts reviewing documents"></div>
  <div class="hero-copy">
    <div class="hero-kicker">Be Found. Be Chosen.</div>
    <h1 class="hero-title"><span class="l1">Empowering <u>High-Ticket</u></span><span class="l2">Service Business Leaders</span></h1>
    <p class="hero-text">Become a Reach Crafter with cutting-edge frameworks and decision-grade intelligence taught in leading business schools. Transform your sales and marketing funnel.</p>
    <a class="btn" href="#">Contact Us <span class="arrow">→</span></a>
  </div>
</section>

<section class="pillars">
  <h2 class="heading sec-title"><span class="accent">Empowering</span> Business Leaders Like You</h2>
  <div class="rule"></div>
  <p class="sub">We provide the tools, frameworks, and intelligence you need to dominate your market.</p>
  <div class="wrap card-row">
    <article class="card pillar">
      <svg viewBox="0 0 62 62" fill="none" stroke="#2d5bf0" stroke-width="2"><circle cx="31" cy="31" r="20"/><circle cx="31" cy="31" r="11"/><circle cx="31" cy="31" r="4"/><path d="M31 5v6M31 51v6M5 31h6M51 31h6M13 13l4 4M45 45l4 4M13 49l4-4M45 17l4-4"/></svg>
      <h3>Cutting-Edge Frameworks</h3><hr>
      <p>Learn the same advanced marketing strategies taught at top business schools, tailored for high-ticket service businesses. Implement proven systems that drive consistent results.</p>
    </article>
    <article class="card pillar">
      <svg viewBox="0 0 62 62" fill="none" stroke="#2d5bf0" stroke-width="2"><circle cx="31" cy="20" r="12"/><path d="M27 17a4 4 0 1 1 5 4v3M31 27v1"/><path d="M31 32v24M31 44l-14-6M31 44l14-6M12 38h6M44 38h6"/></svg>
      <h3>Decision-Grade Intelligence</h3><hr>
      <p>Get data-driven insights to fix leaks in your sales and marketing funnel—fast. We turn complex data into actionable strategies that boost your bottom line.</p>
    </article>
    <article class="card pillar">
      <svg viewBox="0 0 62 62" fill="none" stroke="#2d5bf0" stroke-width="2"><path d="M14 6h24l10 10v30H14z"/><path d="M38 6v10h10M20 24h20M20 31h20M20 38h12"/><circle cx="44" cy="46" r="9"/><path d="M40 46l3 3 5-6"/></svg>
      <h3>Proven Results</h3><hr>
      <p>Become the obvious choice for your ideal clients with positioning that commands premium fees. Join leaders who have transformed their businesses with our guidance.</p>
    </article>
  </div>
</section>

<section class="video">
  <h2 class="heading sec-title">Discover How We <span class="accent">Transform</span> Marketing Funnels</h2>
  <div class="rule"></div>
  <p class="sub">Learn how our proven frameworks help high-ticket service businesses attract premium clients and increase conversion rates.</p>
  <div class="wrap video-frame">
    <div class="video-still" role="img" aria-label="Explainer video still of a busy team of professionals in a modern office">
      <div class="play"><svg width="22" height="24" viewBox="0 0 22 24"><path d="M3 2l17 10L3 22z" fill="#fff"/></svg></div>
    </div>
  </div>
</section>

<section class="stats">
  <div class="stat">
    <div class="stat-ring"><svg viewBox="0 0 192 192"><circle cx="96" cy="96" r="74" fill="none" stroke="#1f3a86" stroke-width="44"/><circle cx="96" cy="96" r="74" fill="none" stroke="#2d5bf0" stroke-width="44" stroke-dasharray="232 465" transform="rotate(-90 96 96)"/><circle cx="96" cy="96" r="50" fill="#0d1a33"/></svg><div class="stat-value">170+</div></div>
    <div class="stat-label">Clients Served</div>
  </div>
  <div class="stat">
    <div class="stat-ring"><svg viewBox="0 0 192 192"><circle cx="96" cy="96" r="74" fill="none" stroke="#1f3a86" stroke-width="44"/><circle cx="96" cy="96" r="74" fill="none" stroke="#2d5bf0" stroke-width="44" stroke-dasharray="232 465" transform="rotate(-90 96 96)"/><circle cx="96" cy="96" r="50" fill="#0d1a33"/></svg><div class="stat-value">53M+</div></div>
    <div class="stat-label">Revenue Generated</div>
  </div>
  <div class="stat">
    <div class="stat-ring"><svg viewBox="0 0 192 192"><circle cx="96" cy="96" r="74" fill="none" stroke="#1f3a86" stroke-width="44"/><circle cx="96" cy="96" r="74" fill="none" stroke="#2d5bf0" stroke-width="44" stroke-dasharray="232 465" transform="rotate(-90 96 96)"/><circle cx="96" cy="96" r="50" fill="#0d1a33"/></svg><div class="stat-value">3.2x</div></div>
    <div class="stat-label">Avg. ROI Increase</div>
  </div>
  <div class="stat">
    <div class="stat-ring"><svg viewBox="0 0 192 192"><circle cx="96" cy="96" r="74" fill="none" stroke="#1f3a86" stroke-width="44"/><circle cx="96" cy="96" r="74" fill="none" stroke="#2d5bf0" stroke-width="44" stroke-dasharray="232 465" transform="rotate(-90 96 96)"/><circle cx="96" cy="96" r="50" fill="#0d1a33"/></svg><div class="stat-value">92%</div></div>
    <div class="stat-label">Client Retention</div>
  </div>
</section>

<section class="about">
  <div class="about-photo" role="img" aria-label="Photo of a focused consultant in a suit writing notes at a desk"></div>
  <div class="about-copy">
    <h2 class="heading about-title">About <span class="brand">REACH CRAFTERS</span></h2>
    <h4>Empowering Business Leaders to Master Demand.</h4>
    <p>At Reach Crafters, we believe every high-ticket service business deserves access to the same strategic frameworks used by top-tier enterprise companies.</p>
    <p>Our team brings together decades of experience in marketing strategy, sales optimization, and business development. We've distilled the best practices from leading business schools and real-world success stories into actionable systems that drive results.</p>
    <a class="btn" href="#">Learn More <span class="arrow">→</span></a>
  </div>
</section>

<section class="reviews">
  <h2 class="heading sec-title">What Our <span class="accent">Happy Clients</span> Say About Us</h2>
  <div class="rule"></div>
  <p class="sub">We provide the tools, frameworks, and intelligence you need to dominate your market.</p>
  <div class="wrap card-row">
    <article class="card review">
      <div class="stars">★★★★★</div><div class="quote-mark">”</div>
      <p>"Reach Crafters helped us identify critical leaks in our funnel that we had overlooked for years. Our lead quality improved by 300% in just 90 days."</p>
      <div class="author"><div class="avatar">K</div><div><strong>Karan Mehlis</strong><span>CEO, Summit Advisory Co.</span></div></div>
    </article>
    <article class="card review">
      <div class="stars">★★★★★</div><div class="quote-mark">”</div>
      <p>"The frameworks provided by Reach Crafters transformed how we approach client acquisition. We've increased our average deal size by 45% while reducing acquisition costs."</p>
      <div class="author"><div class="avatar">D</div><div><strong>Daniel Ortwin</strong><span>Founder, Northline Partners</span></div></div>
    </article>
    <article class="card review">
      <div class="stars">★★★★★</div><div class="quote-mark">”</div>
      <p>"Working with Reach Crafters gave us the clarity and systems we needed to scale efficiently. Their intelligence reports alone have paid for the engagement 10x over."</p>
      <div class="author"><div class="avatar">P</div><div><strong>Priya Valmonte</strong><span>CEO, Summit Advisory Co.</span></div></div>
    </article>
  </div>
  <div class="dots"><i class="on"></i><i></i><i></i><i></i><i></i><i></i></div>
</section>

<section class="blog center">
  <h2 class="heading sec-title">Latest <span class="accent">Blog</span> Posts</h2>
  <div class="rule"></div>
  <div class="wrap card-row" style="text-align:left">
    <article class="card post">
      <div class="post-img a" role="img" aria-label="Photo of a desk with coffee, glasses and a lead funnel sketch"><div class="date"><b>28</b><small>JAN</small></div></div>
      <div class="post-body"><h3>How to 3x Your Lead Quality in 90 Days</h3><p>Proven tactics from top consultants that help you attract premium clients and eliminate time-wasters...</p><span class="more">Learn More →</span></div>
    </article>
    <article class="card post">
      <div class="post-img b" role="img" aria-label="Photo of a hand presenting a rising bar chart"><div class="date"><b>28</b><small>JAN</small></div></div>
      <div class="post-body"><h3>The Hidden Leaks Killing High-Ticket Sales</h3><p>Common mistakes and fixes for service businesses struggling to convert premium prospects into...</p><span class="more">Learn More →</span></div>
    </article>
    <article class="card post">
      <div class="post-img c" role="img" aria-label="Photo of two consultants reviewing a tablet together"><div class="date"><b>28</b><small>JAN</small></div></div>
      <div class="post-body"><h3>Positioning for Premium Clients in 2026</h3><p>Be found. Be chosen. Learn the positioning strategies that make your firm the obvious choice for...</p><span class="more">Learn More →</span></div>
    </article>
  </div>
  <a class="btn" href="#">View All <span class="arrow">→</span></a>
</section>

<section class="cta">
  <h2>Ready to Become a <b>Reach Crafter?</b></h2>
  <p>Schedule a free strategy session and discover how our frameworks can transform your sales and marketing funnel.</p>
  <a class="btn btn-white" href="#">Schedule Your Strategy Call Now <span class="arrow">→</span></a>
</section>

<footer class="site-footer">
  <div class="foot-cols">
    <div class="foot-col foot-brand">
      <div class="brand-name">REACH CRAFTERS</div>
      <p>Lorem ipsum dolor sit amet, consectetur adipiscing elit, sed do</p>
      <div class="follow">Follow Us: <i></i><i class="on"></i><i></i></div>
    </div>
    <div class="foot-col" style="width:179px">
      <h5>Quick Links</h5>
      <ul><li>About us</li><li>Services</li><li>Insights</li><li>Contact Us</li></ul>
    </div>
    <div class="foot-col" style="width:214px">
      <h5>Services</h5>
      <ul><li>Executive Training</li><li>Funnel Optimization</li><li>Demand Generation</li></ul>
    </div>
    <div class="foot-col contact">
      <h5>Contact Details</h5>
      <ul>
        <li><span class="c-icon"><svg width="14" height="16" viewBox="0 0 14 16"><path d="M7 15s5-5 5-9A5 5 0 0 0 2 6c0 4 5 9 5 9z" fill="#0d1a33"/><circle cx="7" cy="6" r="2" fill="#fff"/></svg></span>48 Harbor Lane, Suite 210, Riverton</li>
        <li style="align-items:center"><span class="c-icon" style="background:var(--blue)"><svg width="14" height="14" viewBox="0 0 14 14"><path d="M3 1l2 3-1.5 1.5a8 8 0 0 0 5 5L10 9l3 2-1 2C6 13 1 8 1 2z" fill="#fff"/></svg></span>Phone: (555) 014 2280</li>
        <li style="align-items:center"><span class="c-icon"><svg width="14" height="10" viewBox="0 0 14 10"><rect x="0.5" y="0.5" width="13" height="9" fill="#0d1a33"/><path d="M1 1l6 5 6-5" stroke="#fff" fill="none"/></svg></span>hello@reachcrafters.example</li>
      </ul>
    </div>
  </div>
  <div class="legal">© 2023 Reach Crafters. All rights reserved. | Privacy Policy | Terms of Service</div>
</footer>

</body>
</html>
```